All-Natural Head Lice Removal company

I need a business card with my pre-existing logo. We are a new company located in Portland Oregon that goes into peoples homes to help with head lice removal. My products and approach are all- natural and also will be around children.On my current logo we used Teal Bl and the color Green. I am open to new ideas just want it simple and creative

Target Market(s)

my biggest market is families of school aged children

Industry/Entity Type

Business

Contact Information for Business Card

see upload for details from previous business card

Font styles to use
Serif

Colors
33a6d7
9bcb3b
f37122

Requirements
Must have
• Basic information/ logo put into a creative format that is catching to the eye
Nice to have
• creative

```html
<!DOCTYPE html>
<html lang="en">
<head>
<meta charset="utf-8">
<title>NitClear Business Card</title>
<link href="https://fonts.googleapis.com/css2?family=Arvo:wght@400;700&display=swap" rel="stylesheet">
<style>
  :root {
    --page-bg: #e9e6e1;
    --card-white: #ffffff;
    --card-dark: #2a2a2c;
    --card-dark-deep: #161617;
    --teal-blue: #33a6d7;
    --leaf-green: #9bcb3b;
    --ink: #2b2b2b;
    --light-text: #f2f2f2;
  }
  * { margin: 0; padding: 0; box-sizing: border-box; }
  html, body {
    width: 1200px; height: 913px; overflow: hidden;
    background: var(--page-bg);
    font-family: "Arvo", Georgia, serif;
  }
  .canvas { position: relative; width: 1200px; height: 913px; }
  .card {
    position: absolute; width: 520px; height: 297px;
    border-radius: 16px; overflow: hidden;
    background: var(--card-white);
    box-shadow: 0 10px 26px rgba(0,0,0,.22);
  }
  .card--front { left: 50px; top: 308px; }
  .card--back { left: 630px; top: 308px; }
  .card__shape { position: absolute; inset: 0; }

  .brand { position: absolute; display: flex; align-items: center; gap: 12px; white-space: nowrap; }
  .brand__dot { width: 56px; height: 56px; border-radius: 50%; background: var(--leaf-green); flex: none; }
  .brand__name { font-weight: 700; font-size: 34px; color: var(--ink); letter-spacing: .5px; }
  .card--front .brand { left: 24px; top: 166px; }
  .card--back .brand { left: 50%; top: 52px; transform: translateX(-50%); }

  .front-info { position: absolute; right: 26px; top: 24px; text-align: right; color: var(--light-text); }
  .front-info__service { font-size: 12px; line-height: 1.35; width: 190px; margin-left: auto; }
  .front-info__name { font-size: 16px; font-weight: 700; margin-top: 24px; letter-spacing: .5px; white-space: nowrap; }
  .front-info__role { font-size: 11px; color: var(--teal-blue); letter-spacing: 1px; margin-top: 2px; }
  .contact { list-style: none; margin-top: 18px; font-size: 12.5px; line-height: 1.6; }
  .contact li { display: flex; justify-content: flex-end; align-items: center; gap: 8px; white-space: nowrap; }
  .contact svg { width: 12px; height: 12px; flex: none; }
  .tab {
    position: absolute; right: -14px; top: 78px; width: 28px; height: 28px;
    border-radius: 50%; background: var(--teal-blue);
  }

  .tagline {
    position: absolute; left: 0; right: 0; top: 140px; text-align: center;
    font-size: 13px; font-weight: 700; color: var(--ink); line-height: 1.4;
  }
  .tagline span { display: block; }
  .web {
    position: absolute; left: 0; right: 0; bottom: 12px; text-align: center;
    font-size: 13px; color: var(--teal-blue); letter-spacing: .5px;
  }
</style>
</head>
<body>
<main class="canvas">

  <section class="card card--front" aria-label="Card front">
    <svg class="card__shape" viewBox="0 0 520 297" preserveAspectRatio="none">
      <defs>
        <linearGradient id="darkFront" x1="0" y1="0" x2="1" y2="1">
          <stop offset="0" stop-color="#2a2a2c"/>
          <stop offset="1" stop-color="#161617"/>
        </linearGradient>
      </defs>
      <rect width="520" height="297" fill="url(#darkFront)"/>
      <path d="M0,0 L150,0 C260,40 310,160 318,297 L0,297 Z" fill="#ffffff"/>
      <path d="M154,0 C266,40 316,160 324,297" fill="none" stroke="#33a6d7" stroke-width="4"/>
    </svg>
    <div class="tab"></div>
    <div class="brand">
      <span class="brand__dot"></span>
      <span class="brand__name">NitClear</span>
    </div>
    <div class="front-info">
      <p class="front-info__service">All Natural In-Home Lice Removal Services</p>
      <p class="front-info__name">MAREN WHITFIELD</p>
      <p class="front-info__role">OWNER</p>
      <ul class="contact">
        <li>1-855-555-NITS (6487)
          <svg viewBox="0 0 12 12"><path d="M2.5 1 L4.5 1 L5.3 3.6 L4 4.6 C4.7 6 6 7.3 7.4 8 L8.4 6.7 L11 7.5 L11 9.5 C11 10.3 10.3 11 9.5 11 C5 11 1 7 1 2.5 C1 1.7 1.7 1 2.5 1 Z" fill="#33a6d7"/></svg>
        </li>
        <li>Maren@NitClear.com
          <svg viewBox="0 0 12 12"><rect x="1" y="2.5" width="10" height="7" rx="1" fill="none" stroke="#33a6d7" stroke-width="1.3"/><path d="M1.5 3 L6 6.5 L10.5 3" fill="none" stroke="#33a6d7" stroke-width="1.3"/></svg>
        </li>
        <li>www.NitClear.com
          <svg viewBox="0 0 12 12"><circle cx="6" cy="6" r="5" fill="none" stroke="#33a6d7" stroke-width="1.2"/><ellipse cx="6" cy="6" rx="2.2" ry="5" fill="none" stroke="#33a6d7" stroke-width="1"/><path d="M1 6 H11" stroke="#33a6d7" stroke-width="1"/></svg>
        </li>
      </ul>
    </div>
  </section>

  <section class="card card--back" aria-label="Card back">
    <svg class="card__shape" viewBox="0 0 520 297" preserveAspectRatio="none">
      <path d="M0,297 L0,276 C200,274 430,252 520,196 L520,297 Z" fill="#2a2a2c"/>
      <path d="M0,272 C200,270 428,248 520,190" fill="none" stroke="#33a6d7" stroke-width="4"/>
    </svg>
    <div class="brand">
      <span class="brand__dot"></span>
      <span class="brand__name">NitClear</span>
    </div>
    <p class="tagline">
      <span>Try NitClear Today and Be Lice Free Tomorrow!</span>
      <span>All Natural In-Home Lice Removal Services</span>
    </p>
    <p class="web">www.NitClear.com</p>
  </section>

</main>
</body>
</html>
```